Business Card for beauty technology startup

Design Glimora Business Card for a Beauty, based on the website identity and colors (https://www.glimora-example.com).
Glimora is a beauty tech startup that gathers helpful product info for beauty lovers and consumers (such as availability on stores, price range and product reviews) for makeup products. The card design must be young, colorful but clean, and very modern.

Target Market(s)

woman, 15-35

Industry/Entity Type

Cosmetics

Contact Information for Business Card

Full Name, address, phone

Font styles to use
Other font styles liked:
• Advent Pro

Colors
e34297
86cfc6
ffffff
5c5c5c
e8e8e8
e667a6
b2b2b2

Requirements
Must have
• One full colored side with a creative design and another with card info
• Use Color palette: #95C5C5 and/or #D38AA5
• Use fonts: Advent Pro
• Use website identity: https://www.glimora-example.com
Nice to have
• If needed extra font: Roboto

```html
<!DOCTYPE html>
<html lang="en">
<head>
<meta charset="utf-8">
<title>Glimora Business Card</title>
<link rel="stylesheet" href="https://fonts.googleapis.com/css2?family=Jost:wght@300&family=Open+Sans:wght@400;700&display=swap">
<style>
  :root {
    --teal: #7cc7c6;
    --teal-soft: #b9e2e1;
    --white: #ffffff;
    --backdrop: #e8e8e8;
  }
  * { margin: 0; padding: 0; box-sizing: border-box; }
  html, body { width: 1200px; height: 900px; overflow: hidden; }
  body {
    position: relative;
    background: var(--backdrop);
    font-family: "Open Sans", Arial, sans-serif;
    color: var(--white);
  }
  .card { position: absolute; overflow: hidden; }

  /* Front: contact side */
  .card-front {
    left: 78px; top: 34px; width: 587px; height: 363px;
    background: var(--teal);
  }
  .front-decoration {
    position: absolute; left: 232px; top: 0; width: 355px; height: 100%;
    background: linear-gradient(115deg, var(--teal) 0%, var(--teal-soft) 55%, var(--white) 100%);
  }
  .holder { position: absolute; left: 31px; top: 44px; }
  .holder-name { font-size: 19px; font-weight: 700; letter-spacing: 0.2px; line-height: 1.1; }
  .holder-role { font-size: 15px; line-height: 1.2; }
  .contact-list { position: absolute; left: 31px; top: 205px; list-style: none; font-size: 15px; line-height: 21.5px; }
  .contact-list li { display: flex; align-items: center; gap: 8px; }
  .contact-list svg { width: 11px; height: 11px; fill: var(--white); flex: none; }
  .address { position: absolute; left: 31px; top: 286px; font-size: 15px; line-height: 22px; font-style: normal; }

  /* Back: brand side */
  .card-back {
    left: 388px; top: 505px; width: 567px; height: 352px;
    background: var(--teal);
  }
  .brand {
    position: absolute; left: 0; right: 0; top: 130px;
    display: flex; justify-content: center; align-items: center; gap: 28px;
  }
  .brand-dot { width: 86px; height: 86px; border: 2px solid var(--white); border-radius: 50%; flex: none; }
  .brand-name {
    font-family: "Jost", "Open Sans", sans-serif;
    font-weight: 300; font-size: 64px; letter-spacing: 5px; line-height: 1;
  }
  .back-url {
    position: absolute; left: 0; right: 0; top: 289px;
    text-align: center; font-size: 16px; letter-spacing: 0.5px;
  }
</style>
</head>
<body>
  <section class="card card-front">
    <div class="front-decoration" role="img" aria-label="Large decorative brand monogram in white on teal"></div>
    <div class="holder">
      <p class="holder-name">DANIEL HARTLEY</p>
      <p class="holder-role">Managing Director</p>
    </div>
    <ul class="contact-list">
      <li><svg viewBox="0 0 24 24"><path d="M6.6 10.8a15.1 15.1 0 0 0 6.6 6.6l2.2-2.2c.3-.3.7-.4 1-.2 1.1.4 2.3.6 3.6.6.6 0 1 .4 1 1V20c0 .6-.4 1-1 1A17 17 0 0 1 3 4c0-.6.4-1 1-1h3.5c.6 0 1 .4 1 1 0 1.3.2 2.5.6 3.6.1.3 0 .7-.2 1z"/></svg>(044)987650123</li>
      <li><svg viewBox="0 0 24 24"><path d="M2 5h20v14H2z M4 7v.5l8 5 8-5V7z" fill-rule="evenodd"/></svg>hello@glimora-example.com</li>
      <li><svg viewBox="0 0 24 24"><circle cx="12" cy="12" r="10"/></svg>www.glimora-example.com</li>
    </ul>
    <address class="address">1234, Address GoesHere,<br>Country name, 12345</address>
  </section>

  <section class="card card-back">
    <div class="brand">
      <span class="brand-dot"></span>
      <span class="brand-name">GLIMORA</span>
    </div>
    <p class="back-url">www.glimora-example.com</p>
  </section>
</body>
</html>
```